Website for IT consulting Company

I need a website upgrade, the existing site content is ok, I would also like to add a testimonial page, the site should be something that is easy for us to update content. You use the content from www.kelvanbrook.com as an example. I will also post update logo and artwork. I also need a contact form with some type of validation or captcha.

I added Coded to the Project

Please omit Address maps

Target Market(s)

small business, service oriented companies. We provide IT Consulting, support and mangement

Industry/Entity Type

Information Technology

Coding

Number of Pages Required

1 page

Font styles to use
Serif
Sans Serif

Requirements
Must have
• Contain logo attached, and content from existing web site www.kelvanbrook.com.
• Also need to update content easily, and be movable to different platforms.
• There is a catch phrase
• "Let us worry about your technology…” “ so you don’t have to!”
• Should be included.
Nice to have
• Testimonial page, Project page where we can post new and past projects and pictures
Should not have
• none

```html
<!DOCTYPE html>
<html lang="en">
<head>
<meta charset="utf-8">
<title>Kelvanbrook — IT Solutions</title>
<link rel="stylesheet" href="https://fonts.googleapis.com/css2?family=Fira+Sans+Condensed:wght@400;500&family=Open+Sans:wght@400;600;700&family=Great+Vibes&display=swap">
<style>
  :root{
    --blue:#1a7ac4;
    --blue-dark:#1566a6;
    --ink:#222;
    --text:#555;
    --black:#000;
    --white:#fff;
    --grey-band:#efefef;
    --hero-a:#3c4a5e;
    --hero-b:#7d8796;
    --band-a:#b9cbe4;
    --band-b:#dfe7f3;
  }
  *{box-sizing:border-box;margin:0;padding:0}
  html,body{width:1200px;height:2835px;overflow:hidden;background:var(--white)}
  body{position:relative;font-family:"Open Sans",sans-serif;color:var(--text)}
  .abs{position:absolute}

  /* header */
  .site-header{left:0;top:0;width:1200px;height:120px;background:var(--black)}
  .brand{display:flex;align-items:center;gap:12px}
  .brand-mark{width:44px;height:44px;background:var(--blue);border-radius:6px}
  .brand-name{font-family:"Fira Sans Condensed",sans-serif;font-weight:500;font-size:46px;color:var(--white);letter-spacing:1px;line-height:1}
  .brand-tag{font-size:11px;color:#9bb6cc;margin-top:2px}
  .header-brand{left:100px;top:28px}
  .contact-line{right:100px;top:28px;display:flex;gap:60px;color:var(--white);font-size:17px}
  .contact-line span{display:flex;align-items:center;gap:14px}
  .main-nav{right:100px;top:76px;display:flex;gap:44px;font-size:17px;color:var(--white)}

  /* hero */
  .hero{left:0;top:120px;width:1200px;height:665px;
    background:linear-gradient(120deg,var(--hero-a),var(--hero-b) 55%,#aab2bd);
    clip-path:polygon(0 0,100% 0,100% 100%,0 74%)}
  .hero-title{left:0;top:160px;width:1200px;text-align:center;font-family:"Fira Sans Condensed",sans-serif;font-weight:500;font-size:72px;line-height:88px;color:var(--white)}
  .btn{display:inline-flex;align-items:center;justify-content:center;background:var(--blue);color:var(--white);font-family:"Fira Sans Condensed",sans-serif;font-weight:500}
  .hero-btn{left:513px;top:471px;width:190px;height:52px;font-size:28px}

  /* intro */
  .section-title{font-family:"Fira Sans Condensed",sans-serif;font-weight:500;color:var(--blue);font-size:34px}
  .section-sub{font-family:"Fira Sans Condensed",sans-serif;font-weight:500;color:var(--ink);font-size:25px}
  .center{left:0;width:1200px;text-align:center}
  .intro-text{left:180px;top:918px;width:840px;text-align:center;font-size:12.5px;line-height:22px}
  .small-btn{height:36px;padding:0 14px;font-family:"Open Sans",sans-serif;font-weight:600;font-size:16px;gap:6px}

  /* support band */
  .support-band{left:0;top:1157px;width:1200px;height:453px;background:radial-gradient(circle at 20% 40%,var(--band-b),var(--band-a) 70%)}
  .support-photo{left:756px;top:1157px;width:444px;height:453px;background:linear-gradient(180deg,#9fb6d3,#c8d6e8)}
  .support-text{left:100px;top:1365px;width:530px;font-size:14.5px;line-height:26px;color:#444}

  /* services */
  .service-card{top:1795px;width:306px;height:246px}
  .card-a{left:100px;background:linear-gradient(135deg,#c9a57a,#5a5e66)}
  .card-b{left:446px;background:linear-gradient(135deg,#6b5048,#a08276);display:flex;flex-direction:column;align-items:center;justify-content:center;color:var(--white);font-weight:700;font-size:22px;text-align:center;line-height:34px}
  .card-c{left:796px;background:linear-gradient(135deg,#2f4f82,#8e6a52)}
  .card-b .icons{display:flex;gap:36px;margin-top:10px}

  /* testimonial */
  .quote-bar{left:0;top:2117px;width:1200px;height:79px;background:var(--blue);color:var(--white);font-weight:700;font-size:22px;display:flex;align-items:center;justify-content:center}
  .quote-area{left:0;top:2196px;width:1200px;height:300px;background:var(--grey-band)}
  .quote-text{left:157px;top:2290px;width:625px;font-size:15px;line-height:27px;color:#444}
  .quote-mark{font-size:34px;color:#333;line-height:0;vertical-align:-6px}
  .signature{left:620px;top:2396px;font-family:"Great Vibes",cursive;font-size:44px;color:var(--blue)}
  .avatar{left:869px;top:2281px;width:174px;height:174px;border-radius:50%;background:linear-gradient(180deg,#5a3b2c,#d9b6a0)}

  /* footer */
  .site-footer{left:0;top:2410px;width:1200px;height:425px;background:var(--black);clip-path:polygon(0 0,100% 150px,100% 100%,0 100%)}
  .footer-brand{left:0;top:2570px;width:1200px;display:flex;justify-content:center}
  .socials{left:0;top:2656px;width:1200px;display:flex;justify-content:center;gap:14px}
  .socials span{width:40px;height:40px;border-radius:50%;background:var(--white)}
  .footer-nav{left:0;top:2726px;width:1200px;display:flex;justify-content:center;gap:100px;color:var(--white);font-size:12px}
  .footer-rule{left:100px;top:2773px;width:1000px;height:1px;background:#555}
  .copyright{left:0;top:2802px;width:1200px;text-align:center;color:var(--white);font-size:12px}
</style>
</head>
<body>

<header class="site-header abs">
  <div class="header-brand brand abs">
    <div class="brand-mark"></div>
    <div>
      <div class="brand-name">KELVANBROOK</div>
      <div class="brand-tag">Let us worry about your technology… So you don't have to!</div>
    </div>
  </div>
  <div class="contact-line abs">
    <span><svg width="16" height="16" viewBox="0 0 16 16"><rect width="16" height="16" rx="2" fill="#fff"/><path d="M4 3.5c0 5 3.5 8.5 8.5 8.5l.5-2-2.5-1-1 1c-1.5-.7-2.3-1.5-3-3l1-1-1-2.5z" fill="#000"/></svg>555 014 2290</span>
    <span><svg width="18" height="14" viewBox="0 0 18 14"><rect width="18" height="14" rx="1" fill="#fff"/><path d="M1 1l8 6 8-6" stroke="#000" stroke-width="1.5" fill="none"/></svg>info@kelvanbrook.com</span>
  </div>
  <nav class="main-nav abs">
    <span>Home</span><span>About Us</span><span>Support</span><span>Clients</span><span>Careers</span><span>Contact Us</span>
  </nav>
</header>

<section class="hero abs" role="img" aria-label="Team working at a desk with laptops, charts and technology overlay"></section>
<h1 class="hero-title abs">Flexible Solutions For Your<br>Business Needs</h1>
<span class="btn hero-btn abs">CONTACT US</span>

<h2 class="section-title center abs" style="top:802px">IT Solutions That Work For Your Business</h2>
<h3 class="section-sub center abs" style="top:853px">A Full Service Technology&nbsp; Company</h3>
<p class="intro-text abs">Kelvanbrook is a technology solution provider based in Houston, Texas. Our goal is to make technology a non-issue for individuals and small to medium size businesses ranging from 5 to 150 Users. Kelvanbrook has the experience, the tools, high-level technology solutions and training to power your business and your work force. We understand that all business's have one goal in common Outsourcing is subcontracting a process, such as product design or manufacturing, to a third-party company.[1] The decision to outsource is often made in the interest of lowering firm costs, redirecting or conserving energy directed at the competencies of a particular business, or to make more efficient use of land, labor, capital, (information) technology and resources. Outsourcing became part of the business lexicon during the 1980s.</p>
<span class="btn small-btn abs" style="left:537px;top:1069px">Read More <svg width="6" height="10" viewBox="0 0 6 10"><path d="M0 0l6 5-6 5z" fill="#fff"/></svg></span>

<section class="support-band abs"></section>
<div class="support-photo abs" role="img" aria-label="Two colleagues in office wear looking at a laptop"></div>
<h2 class="section-title abs" style="left:100px;top:1240px">IT Support Solutions</h2>
<h3 class="section-sub abs" style="left:100px;top:1306px">A Return on Investment</h3>
<p class="support-text abs">Our goal is to make technology a non-issue for individuals and small to medium size businesses ranging from 5 to 150 Users. Kelvanbrook has the experience, the tools, high-level technology solutions and training to power your business and your work force.</p>
<span class="btn small-btn abs" style="left:100px;top:1487px">Read More <svg width="6" height="10" viewBox="0 0 6 10"><path d="M0 0l6 5-6 5z" fill="#fff"/></svg></span>

<h2 class="section-title center abs" style="top:1672px">Let Us Worry About Your Technology</h2>
<h3 class="section-sub center abs" style="top:1723px">So You Don't Have To</h3>
<div class="service-card card-a abs" role="img" aria-label="Support agent with headset working at a laptop"></div>
<div class="service-card card-b abs" role="img" aria-label="Remote diagnostic and support service">
  <div>Remote Diagnostic &amp;<br>Support</div>
  <div class="icons">
    <svg width="16" height="22" viewBox="0 0 16 22"><circle cx="8" cy="3" r="2.5" fill="#fff"/><rect x="5" y="8" width="6" height="13" fill="#fff"/></svg>
    <svg width="22" height="22" viewBox="0 0 22 22"><circle cx="9" cy="9" r="6.5" stroke="#fff" stroke-width="3" fill="none"/><path d="M14 14l6 6" stroke="#fff" stroke-width="3.5"/><path d="M6 9h6M9 6v6" stroke="#fff" stroke-width="2"/></svg>
  </div>
</div>
<div class="service-card card-c abs" role="img" aria-label="Network switch with blue and red patch cables"></div>

<div class="quote-bar abs">What Client Say's About KELVANBROOK</div>
<section class="quote-area abs"></section>
<p class="quote-text abs"><span class="quote-mark">“</span> Lorem Ipsum is simply dummy text of the printing and typesetting industry. Lorem Ipsum has been the industry's standard dummy text ever since the 1500s, when an unknown printer took a galley of type and scrambled.Lorem Ipsum is simply dummy text of the printing and typesetting industry <span class="quote-mark">”</span></p>
<div class="avatar abs" role="img" aria-label="Portrait of the client"></div>

<footer class="site-footer abs"></footer>
<div class="signature abs">Lena Marlow</div>
<div class="footer-brand abs">
  <div class="brand">
    <div class="brand-mark" style="background:#fff"></div>
    <div>
      <div class="brand-name">KELVANBROOK</div>
      <div class="brand-tag" style="color:#ccc">Let us worry about your technology… So you don't have to!</div>
    </div>
  </div>
</div>
<div class="socials abs"><span></span><span></span><span></span></div>
<nav class="footer-nav abs"><span>Home</span><span>About Us</span><span>Clients</span><span>Support</span><span>Contact Us</span></nav>
<div class="footer-rule abs"></div>
<p class="copyright abs">Copyright © 2017 - Kelvanbrook Group, Inc - All rights reserved</p>

</body>
</html>
```